Tollin Waste Website Design

Our new start-up needs a website design. We plan to help businesses find more sustainable ways to manage their waste. Our initial website aims to gather contact data from potential business customers and comprehensive information from waste facilities and waste transporters. We have a logo design (attached) which we would like included in the website design. I have also attached a number of pages that describe what information should appear on each page as well as a web design brief file that describes the look we are after.

```html
<!DOCTYPE html>
<html lang="en">
<head>
<meta charset="utf-8">
<title>Tollin Waste – Home</title>
<link rel="stylesheet" href="https://fonts.googleapis.com/css2?family=Poppins:wght@400;500&family=Ubuntu:wght@400;700&family=Roboto:wght@400&display=swap">
<style>
  :root {
    --board: #cfe3b7;
    --green: #6aa82a;
    --green-dark: #5a9a1e;
    --white: #ffffff;
    --ink: #2a2a2a;
    --muted: #444444;
    --footer: rgba(20, 14, 14, 0.72);
    --overlay: rgba(0, 0, 0, 0.62);
  }
  * { box-sizing: border-box; margin: 0; padding: 0; }
  html, body { width: 900px; height: 1200px; overflow: hidden; }
  body { background: var(--board); position: relative; font-family: "Poppins", sans-serif; }

  .screen {
    position: absolute; left: 38px; width: 822px; height: 496px; overflow: hidden;
  }
  .screen--home { top: 74px; }
  .screen--signup { top: 619px; }

  .hero-photo {
    position: absolute; inset: 0;
    background:
      linear-gradient(180deg, rgba(0,0,0,0.1) 0%, rgba(0,0,0,0.25) 100%),
      linear-gradient(180deg, #2b4f86 0%, #36619c 18%, #6d7a84 38%, #8a9196 52%, #6c5a57 68%, #6b3333 84%, #3d2222 100%);
  }

  .site-header { position: absolute; top: 0; left: 0; right: 0; height: 70px; }
  .brand {
    position: absolute; left: 62px; top: 24px; display: flex; align-items: center; gap: 6px;
    font-family: "Ubuntu", sans-serif; font-weight: 700; font-size: 14px; color: var(--white);
    white-space: nowrap;
  }
  .brand-dot { width: 22px; height: 22px; border: 3px solid var(--green); border-radius: 50%; flex: none; }
  .main-nav { position: absolute; left: 215px; top: 28px; display: flex; gap: 20px; white-space: nowrap; }
  .main-nav a { color: var(--white); text-decoration: none; font-size: 10.5px; }
  .social { position: absolute; left: 662px; top: 24px; display: flex; gap: 6px; }
  .social span { width: 20px; height: 20px; border: 1px solid var(--white); border-radius: 50%; display: block; }

  .hero-title {
    position: absolute; top: 116px; left: 0; right: 0; text-align: center; color: var(--white);
    font-family: "Ubuntu", sans-serif; font-weight: 700; font-size: 36px; letter-spacing: -0.5px;
  }
  .hero-sub {
    position: absolute; top: 170px; left: 0; right: 0; text-align: center; color: var(--white);
    font-family: "Ubuntu", sans-serif; font-size: 27px;
  }

  .roles { position: absolute; top: 236px; left: 0; width: 100%; height: 130px; }
  .role {
    position: absolute; top: 0; width: 128px; height: 128px; border-radius: 50%;
    border: 6px solid var(--green); background: rgba(25, 25, 25, 0.72);
    display: flex; flex-direction: column; align-items: center; justify-content: center;
    color: var(--white); font-family: "Poppins", sans-serif; font-size: 15px; line-height: 1.2; text-align: center;
  }
  .role svg { margin-bottom: 6px; }
  .role--producers { left: 179px; }
  .role--facilities { left: 340px; }
  .role--transporters { left: 502px; }

  .site-footer {
    position: absolute; left: 0; right: 0; bottom: 0; height: 59px; background: var(--footer);
    border-top: 1px solid rgba(255,255,255,0.35);
    display: flex; align-items: center; justify-content: center;
    color: var(--white); font-family: "Roboto", sans-serif; font-size: 12.5px;
  }

  .overlay { position: absolute; inset: 0; background: var(--overlay); }
  .signup-modal {
    position: absolute; left: 142px; top: 100px; width: 538px; height: 287px;
    background: var(--white); border-radius: 12px; text-align: center;
  }
  .modal-close { position: absolute; left: 507px; top: 12px; }
  .modal-brand {
    position: absolute; top: 30px; left: 0; right: 0; display: flex; justify-content: center; align-items: center; gap: 10px;
    font-family: "Poppins", sans-serif; font-weight: 500; font-size: 30px; color: var(--ink); white-space: nowrap;
  }
  .modal-brand .brand-dot { width: 44px; height: 44px; border-width: 4px; }
  .modal-title {
    position: absolute; top: 98px; left: 0; right: 0;
    font-family: "Poppins", sans-serif; font-weight: 500; font-size: 24px; color: #111;
  }
  .modal-text {
    position: absolute; top: 131px; left: 0; right: 0;
    font-family: "Roboto", sans-serif; font-size: 13.5px; line-height: 22px; color: var(--muted);
  }
  .signup-form {
    position: absolute; left: 53px; top: 198px; width: 431px; height: 44px;
    border: 1px solid #555; border-radius: 22px; display: flex; align-items: center; padding: 0 3px 0 19px;
  }
  .signup-form label { flex: 1; text-align: left; font-family: "Roboto", sans-serif; font-size: 12px; color: #222; }
  .signup-btn {
    width: 80px; height: 36px; border: none; border-radius: 18px; background: var(--green-dark);
    color: var(--white); font-family: "Poppins", sans-serif; font-size: 16px;
  }
</style>
</head>
<body>

<section class="screen screen--home">
  <div class="hero-photo" role="img" aria-label="Photo of blue and green waste drums and a skip full of old batteries"></div>
  <header class="site-header">
    <div class="brand"><span class="brand-dot"></span>TOLLIN WASTE</div>
    <nav class="main-nav"><a href="#">About us</a><a href="#">What we do</a><a href="#">Resources</a><a href="#">Contact us</a></nav>
    <div class="social"><span></span><span></span><span></span><span></span></div>
  </header>
  <h1 class="hero-title">WELCOME TO TOLLIN WASTE</h1>
  <p class="hero-sub">Take control of your waste here</p>
  <div class="roles">
    <a class="role role--producers">
      <svg width="22" height="30" viewBox="0 0 22 30"><path d="M2 7h18M8 7V3h6v4M4 7l2 21h10l2-21" fill="none" stroke="#6aa82a" stroke-width="2.5"/><path d="M9 11v14M13 11v14" stroke="#6aa82a" stroke-width="2"/></svg>
      Waste<br>Producers
    </a>
    <a class="role role--facilities">
      <svg width="30" height="30" viewBox="0 0 30 30"><path d="M15 4a11 11 0 1 1-10 6" fill="none" stroke="#6aa82a" stroke-width="4"/><path d="M1 8l5 6 4-7z" fill="#6aa82a"/></svg>
      Waste<br>Facilities
    </a>
    <a class="role role--transporters">
      <svg width="44" height="26" viewBox="0 0 44 26"><rect x="1" y="2" width="28" height="16" fill="#6aa82a"/><path d="M30 7h8l5 6v5H30z" fill="#6aa82a"/><circle cx="9" cy="21" r="4" fill="#6aa82a" stroke="#222" stroke-width="1.5"/><circle cx="36" cy="21" r="4" fill="#6aa82a" stroke="#222" stroke-width="1.5"/></svg>
      Waste<br>Transporters
    </a>
  </div>
  <footer class="site-footer">Copyright © 2018. All Rights Reserved</footer>
</section>

<section class="screen screen--signup">
  <div class="hero-photo" role="img" aria-label="Photo of blue and green waste drums and a skip full of old batteries"></div>
  <header class="site-header">
    <div class="brand"><span class="brand-dot"></span>TOLLIN WASTE</div>
    <nav class="main-nav"><a href="#">About us</a><a href="#">What we do</a><a href="#">Resources</a><a href="#">Contact us</a></nav>
    <div class="social"><span></span><span></span><span></span><span></span></div>
  </header>
  <footer class="site-footer">Copyright © 2018. All Rights Reserved</footer>
  <div class="overlay"></div>
  <div class="signup-modal">
    <svg class="modal-close" width="20" height="20" viewBox="0 0 20 20"><circle cx="10" cy="10" r="9" fill="none" stroke="#222" stroke-width="1.2"/><path d="M6 6l8 8M14 6l-8 8" stroke="#222" stroke-width="1.2"/></svg>
    <div class="modal-brand"><span class="brand-dot"></span>TOLLIN WASTE</div>
    <h2 class="modal-title">Welcome to Tollin Waste.</h2>
    <p class="modal-text">We are just getting started. Please register your email address<br>to receive updates from us</p>
    <form class="signup-form"><label>Email address</label><button class="signup-btn" type="button">Signup</button></form>
  </div>
</section>

</body>
</html>
```